Cybersecurity Company Profile Word Template

We are looking for designs to develop a modern, innovative, and Company Profile template. This template will be a Word template that we will convert to PDF and send to potential clients and partners. The ideal structure of the template can be found below. We would like to see designs that relate to cybersecurity and include our company colors white, black, and red (#A80402). We have attached the logo we plan to use as we are rebranding. Additionally, I have included our logo variations. Company website is https://vornelquay.io. For content placeholder text is fine. We are concerned with the overall template having the necessary sections, pages, and overall structure we have mentioned in this brief.

Ideal template flow and structure:
-Cover Page
-Company "Contact Us"
-Table of Contents
-About Company
- NAICS Codes
- 541519 - Other Computer Related Servcies
- 541512 - Computer Systems Design Services
- 541690 - Other Scientific and Technical Consulting Services
- 541511 - Custom Computer Programming Services
-CEO Statement/Message (picture/headshot will be added to this page)
-Company History
-Vision and Misson
-Team Bios- Bio will include a picrure
-Our Values
- (Short paragraph)
- Our Services
- Penetration Testing
- Red Team/Threat Emulation
- Cloud Security Assessments
- Vulnerability Management
- Managed Detection and Response
- Incident Response
- Threat Hunting
- Risk Assessments
- Simulated Phishing Campaigns
- Projects

Target Market(s)

Potential customers and partners

Industry/Entity Type

Cybersecurity

Colors

Designer to choose colors to be used in the design.

Requirements
Must have
• Red must be #a80402

```html
<!DOCTYPE html>
<html lang="en">
<head>
<meta charset="utf-8">
<title>Vornelquay Security – Company Profile Template</title>
<link rel="stylesheet" href="https://fonts.googleapis.com/css2?family=Archivo:wght@400;600;800&family=Orbitron:wght@700&display=swap">
<style>
:root{
  --red:#a80402;
  --red-bright:#d1201c;
  --ink:#141414;
  --ink-soft:#2a2a2a;
  --paper:#f3f3f3;
  --paper-grey:#c9c9c9;
  --canvas:#e4e5e7;
  --text:#333;
  --muted:#8a8a8a;
}
*{box-sizing:border-box;margin:0;padding:0}
html,body{width:758px;height:1200px;overflow:hidden}
body{background:var(--canvas);font-family:"Archivo",Arial,sans-serif;color:var(--text);position:relative}

.sheet{position:absolute;display:flex}
.page{position:relative;width:156px;height:234px;background:var(--paper);overflow:hidden}
.page + .page{border-left:1px solid #dcdcdc}

.page-head{position:absolute;left:0;top:0;right:0;height:22px;background:var(--ink);display:flex;align-items:center;justify-content:space-between;padding:0 10px}
.brand{display:flex;align-items:center;gap:3px;color:#fff;font-weight:600;font-size:5px;letter-spacing:1px}
.brand-mark{width:5px;height:5px;background:var(--red)}
.folio{font-size:3px;color:#bbb}

.photo{position:absolute;background:radial-gradient(circle at 55% 45%,#c4231f 0%,#6b0a08 35%,#1c0707 75%,#0d0d0d 100%)}
.photo.dark{background:radial-gradient(circle at 60% 50%,#8e100d 0%,#3a0706 40%,#111 80%)}
.photo.strip{background:linear-gradient(90deg,#1a0505,#7e0b09 50%,#1a0505)}
.photo.column{background:linear-gradient(180deg,#2a0605,#7e0b09 40%,#1a0505 70%,#4a0807)}

.section-title{position:absolute;font-weight:800;font-size:13px;line-height:1.12;color:var(--ink);letter-spacing:.2px}
.rule{position:absolute;height:1px;background:var(--red)}
.body-copy{position:absolute;font-size:2.9px;line-height:1.45;color:#444;text-align:justify}
.body-copy p + p{margin-top:3px}

/* cover */
.cover{width:166px}
.cover-art{position:absolute;left:0;top:0;width:166px;height:118px;background:radial-gradient(circle at 50% 48%,#e01f1a 0%,#a80402 14%,#3a0504 32%,#151515 60%,#0c0c0c 100%)}
.cover-date{position:absolute;left:13px;top:12px;background:var(--red);color:#fff;font-size:6px;padding:4px 5px}
.cover .brand{position:absolute;right:9px;top:17px}
.cover-title{position:absolute;left:0;right:0;top:133px;text-align:center;font-family:"Orbitron",sans-serif;font-weight:700;font-size:14.5px;line-height:1.45;color:var(--ink)}
.cover-sub{position:absolute;left:19px;top:183px;font-weight:800;font-size:5px;line-height:1.8;color:var(--ink)}
.cover-foot{position:absolute;left:0;right:0;bottom:0;height:22px;background:var(--red);display:flex;align-items:center;justify-content:space-between;padding:0 19px;color:#fff;font-size:2.8px}
.back{width:165px;background:#121212}
.back-art{position:absolute;inset:0;background:radial-gradient(circle at 50% 42%,#e01f1a 0%,#a80402 10%,#3d0504 24%,#171717 52%,#0c0c0c 100%)}
.back-url{position:absolute;top:23px;left:0;right:0;text-align:center;color:#ddd;font-size:5.5px}
.back .brand{position:absolute;left:0;right:0;bottom:22px;justify-content:center;font-size:10px;gap:6px;letter-spacing:2.5px}
.back .brand-mark{width:10px;height:10px}

/* contact */
.contact-list{position:absolute;left:14px;top:174px;list-style:none}
.contact-list li{display:flex;align-items:center;gap:8px;height:11.5px;font-size:3.3px;color:#333}
.contact-list svg{width:6px;height:6px}

/* toc */
.toc{position:absolute;left:14px;top:112px;width:128px;display:grid;grid-template-columns:1fr 1fr;column-gap:18px}
.toc-item{display:flex;justify-content:space-between;align-items:center;height:12.6px;font-size:3.2px;color:#333}
.toc-num{font-family:"Orbitron",sans-serif;font-size:4.8px;color:#222}

/* about */
.about-panel{position:absolute;left:0;top:22px;width:98px;bottom:0;background:#cfcfcf}

/* naics */
.naics{position:absolute;left:14px;top:188px;display:flex;gap:6px}
.naics-box{width:26px;height:29px;background:var(--red);color:#fff;padding:3px;font-size:2.4px;line-height:1.3}
.naics-code{display:flex;align-items:center;gap:2px;font-size:2.6px;margin-bottom:4px}
.naics-label{text-align:center}

/* ceo */
.ceo-card{position:absolute;left:18px;top:81px;width:27px;text-align:center;font-size:2.9px;line-height:1.5;color:#444}
.ceo-photo{width:27px;height:29px;margin-bottom:5px}
.ceo-card strong{font-weight:800;color:#222}

/* vision */
.sub-head{position:absolute;display:flex;align-items:center;gap:4px;font-weight:800;font-size:7px;color:var(--ink)}
.sub-head svg{width:6px;height:6px}

/* team */
.team{position:absolute;left:12px;top:78px;width:135px;display:grid;grid-template-columns:repeat(3,1fr);column-gap:6px;row-gap:9px}
.member{font-size:2.7px;line-height:1.4;color:#555}
.member-photo{width:25px;height:27px;margin:0 auto 3px;position:relative}
.member-name{text-align:center;font-weight:800;color:#222;font-size:2.8px}
.member-role{text-align:center;font-weight:800;color:#222;margin-bottom:2px}

/* services */
.services{position:absolute;left:19px;top:95px;width:114px;border:1.5px solid var(--red);display:grid;grid-template-columns:repeat(3,1fr);gap:1px;background:var(--red)}
.service{background:#fff;height:42px}
.service-head{background:var(--red);color:#fff;font-size:3.2px;line-height:1.2;text-align:center;padding:2px 2px 0;height:19px;display:flex;flex-direction:column;align-items:center;gap:1px}
.service-head svg{width:6px;height:6px}
.service-copy{font-size:2.6px;line-height:1.35;color:#444;padding:2px;text-align:justify}
</style>
</head>
<body>

<!-- Row 1: front and back cover -->
<section class="sheet" style="left:212px;top:42px">
  <article class="page cover">
    <div class="cover-art" role="img" aria-label="Dark circuit board artwork with a glowing red padlock at its centre"></div>
    <div class="cover-date">JANUARY 2025</div>
    <div class="brand"><span class="brand-mark"></span>VORNELQUAY</div>
    <h1 class="cover-title">COVER PAGE<br>TITLE HERE</h1>
    <p class="cover-sub">COVER PAGE SUBTITLE CAN GO HERE<br>COVER PAGE SUBTITLE CAN GO HERE</p>
    <footer class="cover-foot"><span>Tel: 555.014.2280</span><span>https://vornelquay.io</span><span>secureme@vornelquay.io</span></footer>
  </article>
</section>

<section class="sheet" style="left:423px;top:42px">
  <article class="page back">
    <div class="back-art" role="img" aria-label="Dark circuit board artwork with a glowing red padlock in the middle"></div>
    <p class="back-url">WWW.VORNELQUAY.IO</p>
    <div class="brand"><span class="brand-mark"></span>VORNELQUAY</div>
  </article>
</section>

<!-- Row 2: contact / contents -->
<section class="sheet" style="left:67px;top:325px">
  <article class="page">
    <header class="page-head"><div class="brand"><span class="brand-mark"></span>VORNELQUAY</div><span class="folio">2</span></header>
    <div class="photo" style="left:0;top:22px;width:156px;height:116px" role="img" aria-label="Red lit circuit board with a metal padlock"></div>
    <h2 class="section-title" style="left:18px;top:143px">CONTACT US</h2>
    <div class="rule" style="left:18px;top:162px;width:127px"></div>
    <ul class="contact-list">
      <li><svg viewBox="0 0 10 10" fill="none" stroke="#222" stroke-width=".9"><rect x="1" y="1.5" width="8" height="5.5"/><path d="M3 9h4M5 7v2"/></svg>https://www.vornelquay.io/</li>
      <li><svg viewBox="0 0 10 10" fill="none" stroke="#222" stroke-width=".9"><rect x="1" y="2" width="8" height="6"/><path d="M1 2l4 3.5L9 2"/></svg>secureme@vornelquay.io</li>
      <li><svg viewBox="0 0 10 10" fill="#222"><path d="M5 .5a3.2 3.2 0 0 0-3.2 3.2C1.8 6.2 5 9.5 5 9.5s3.2-3.3 3.2-5.8A3.2 3.2 0 0 0 5 .5zm0 4.5a1.3 1.3 0 1 1 0-2.6 1.3 1.3 0 0 1 0 2.6z"/></svg>1420 Harbor Ln. #210, Eastfield, Florida 33000</li>
      <li><svg viewBox="0 0 10 10" fill="#222"><path d="M2.2 1l1.7 1.9-.9 1.2a6 6 0 0 0 2.9 2.9l1.2-.9L9 7.8 8 9C4.4 9 1 5.6 1 2z"/></svg>555.014.2280</li>
    </ul>
  </article>
  <article class="page">
    <header class="page-head"><div class="brand"><span class="brand-mark"></span>VORNELQUAY</div><span class="folio">3</span></header>
    <h2 class="section-title" style="left:16px;top:60px">TABLE OF<br>CONTENTS</h2>
    <div class="rule" style="left:14px;top:100px;width:126px"></div>
    <div class="toc">
      <div class="toc-item"><span>Lorem ipsum</span><span class="toc-num">01</span></div>
      <div class="toc-item"><span>Lorem ipsum</span><span class="toc-num">07</span></div>
      <div class="toc-item"><span>Lorem ipsum</span><span class="toc-num">02</span></div>
      <div class="toc-item"><span>Lorem ipsum</span><span class="toc-num">08</span></div>
      <div class="toc-item"><span>Lorem ipsum</span><span class="toc-num">03</span></div>
      <div class="toc-item"><span>Lorem ipsum</span><span class="toc-num">09</span></div>
      <div class="toc-item"><span>Lorem ipsum</span><span class="toc-num">04</span></div>
      <div class="toc-item"><span>Lorem ipsum</span><span class="toc-num">10</span></div>
      <div class="toc-item"><span>Lorem ipsum</span><span class="toc-num">05</span></div>
      <div class="toc-item"><span>Lorem ipsum</span><span class="toc-num">11</span></div>
      <div class="toc-item"><span>Lorem ipsum</span><span class="toc-num">06</span></div>
      <div class="toc-item"><span>Lorem ipsum</span><span class="toc-num">12</span></div>
    </div>
    <div class="photo strip" style="left:14px;top:194px;width:126px;height:31px" role="img" aria-label="Banner of red circuitry with a padlock"></div>
  </article>
</section>

<!-- Row 2: about / NAICS -->
<section class="sheet" style="left:395px;top:325px">
  <article class="page">
    <header class="page-head"><div class="brand"><span class="brand-mark"></span>VORNELQUAY</div><span class="folio">4</span></header>
    <div class="about-panel"></div>
    <div class="photo column" style="left:98px;top:22px;width:58px;height:212px" role="img" aria-label="Vertical strip of dark red circuit patterns"></div>
    <h2 class="section-title" style="left:16px;top:30px">ABOUT<br>COMPANY</h2>
    <div class="rule" style="left:16px;top:68px;width:70px"></div>
    <div class="body-copy" style="left:16px;top:76px;width:70px">
      <p>Our team protects the systems, people and data that keep modern organisations running. We combine offensive testing with steady defensive practice so that every client gains a clear view of real risk, a plan to reduce it and a partner who stays close after the report is delivered. Founded by practitioners, the firm grew from a small consulting desk into a full security practice serving public and private clients across many sectors.</p>
      <p>Our team protects the systems, people and data that keep modern organisations running. We combine offensive testing with steady defensive practice so that every client gains a clear view of real risk, a plan to reduce it and a partner who stays close after the report is delivered. Founded by practitioners, the firm grew from a small consulting desk into a full security practice serving public and private clients across many sectors.</p>
    </div>
  </article>
  <article class="page">
    <header class="page-head"><div class="brand"><span class="brand-mark"></span>VORNELQUAY</div><span class="folio">5</span></header>
    <div class="photo dark" style="left:0;top:22px;width:156px;height:112px" role="img" aria-label="Close-up of a processor chip on a red and black circuit board"></div>
    <h2 class="section-title" style="left:18px;top:149px">NAICS CODES</h2>
    <div class="rule" style="left:16px;top:167px;width:124px"></div>
    <div class="naics">
      <div class="naics-box"><div class="naics-code"><svg viewBox="0 0 6 6" width="3" height="3" fill="#fff"><path d="M0 5l3.5-3.5H2V.5h3v3H4V2L.8 5.6z"/></svg>541519</div><div class="naics-label">Other Computer Related Services</div></div>
      <div class="naics-box"><div class="naics-code"><svg viewBox="0 0 6 6" width="3" height="3" fill="#fff"><path d="M0 5l3.5-3.5H2V.5h3v3H4V2L.8 5.6z"/></svg>541512</div><div class="naics-label">Computer Systems Design Services</div></div>
      <div class="naics-box"><div class="naics-code"><svg viewBox="0 0 6 6" width="3" height="3" fill="#fff"><path d="M0 5l3.5-3.5H2V.5h3v3H4V2L.8 5.6z"/></svg>541690</div><div class="naics-label">Other Scientific and Technical Consulting Services</div></div>
      <div class="naics-box"><div class="naics-code"><svg viewBox="0 0 6 6" width="3" height="3" fill="#fff"><path d="M0 5l3.5-3.5H2V.5h3v3H4V2L.8 5.6z"/></svg>541511</div><div class="naics-label">Custom Computer Programming Services</div></div>
    </div>
  </article>
</section>

<!-- Row 3: CEO / history -->
<section class="sheet" style="left:67px;top:618px">
  <article class="page" style="background:#d4d4d4">
    <header class="page-head"><div class="brand"><span class="brand-mark"></span>VORNELQUAY</div><span class="folio">6</span></header>
    <h2 class="section-title" style="left:16px;top:42px">CEO STATEMENT</h2>
    <div class="rule" style="left:16px;top:61px;width:126px"></div>
    <div class="ceo-card">
      <div class="photo ceo-photo" role="img" aria-label="Headshot placeholder of the chief executive"></div>
      <strong>CEO Name</strong><br>Vornelquay<br>Security CEO
    </div>
    <div class="body-copy" style="left:63px;top:79px;width:79px">
      <p>Our team protects the systems, people and data that keep modern organisations running. We combine offensive testing with steady defensive practice so that every client gains a clear view of real risk, a plan to reduce it and a partner who stays close after the report is delivered.</p>
      <p>Founded by practitioners, the firm grew from a small consulting desk into a full security practice serving public and private clients across many sectors.</p>
    </div>
    <div class="photo dark" style="left:16px;top:171px;width:126px;height:57px" role="img" aria-label="Dark panel with a glowing red padlock"></div>
  </article>
  <article class="page">
    <header class="page-head"><div class="brand"><span class="brand-mark"></span>VORNELQUAY</div><span class="folio">7</span></header>
    <div class="photo column" style="left:0;top:22px;width:55px;height:212px" role="img" aria-label="Vertical strip of digital code with red padlocks"></div>
    <div style="position:absolute;left:55px;top:22px;right:0;bottom:0;background:#d0d0d0"></div>
    <h2 class="section-title" style="left:72px;top:30px">COMPANY<br>HISTORY</h2>
    <div class="rule" style="left:72px;top:68px;width:70px"></div>
    <div class="body-copy" style="left:72px;top:76px;width:70px">
      <p>Our team protects the systems, people and data that keep modern organisations running. We combine offensive testing with steady defensive practice so that every client gains a clear view of real risk, a plan to reduce it and a partner who stays close after the report is delivered. Founded by practitioners, the firm grew from a small consulting desk into a full security practice serving public and private clients across many sectors.</p>
      <p>Our team protects the systems, people and data that keep modern organisations running. We combine offensive testing with steady defensive practice so that every client gains a clear view of real risk, a plan to reduce it and a partner who stays close after the report is delivered.</p>
    </div>
  </article>
</section>

<!-- Row 3: vision / team -->
<section class="sheet" style="left:395px;top:618px">
  <article class="page">
    <header class="page-head"><div class="brand"><span class="brand-mark"></span>VORNELQUAY</div><span class="folio">8</span></header>
    <h2 class="section-title" style="left:20px;top:40px">VISION &amp; MISSON</h2>
    <div class="rule" style="left:16px;top:60px;width:126px"></div>
    <div class="sub-head" style="left:20px;top:74px"><svg viewBox="0 0 6 6" fill="var(--red)"><path d="M0 5l3.5-3.5H2V.5h3v3H4V2L.8 5.6z"/></svg>VISION</div>
    <div class="body-copy" style="left:20px;top:85px;width:58px"><p>Our team protects the systems, people and data that keep modern organisations running. We combine offensive testing with steady defensive practice so that every client gains a clear view of real risk, a plan to reduce it and a partner who stays close after the report is delivered.</p></div>
    <div class="photo" style="left:87px;top:70px;width:55px;height:61px" role="img" aria-label="Red glowing circuit board detail"></div>
    <div class="photo" style="left:20px;top:146px;width:60px;height:62px" role="img" aria-label="Red glowing circuit board detail"></div>
    <div class="sub-head" style="left:90px;top:148px"><svg viewBox="0 0 6 6" fill="var(--red)"><path d="M0 5l3.5-3.5H2V.5h3v3H4V2L.8 5.6z"/></svg>MISSON</div>
    <div class="body-copy" style="left:90px;top:159px;width:52px"><p>Our team protects the systems, people and data that keep modern organisations running. We combine offensive testing with steady defensive practice so that every client gains a clear view of real risk, a plan to reduce it and a partner who stays close after the report is delivered.</p></div>
  </article>
  <article class="page">
    <header class="page-head"><div class="brand"><span class="brand-mark"></span>VORNELQUAY</div><span class="folio">9</span></header>
    <h2 class="section-title" style="left:16px;top:43px;font-size:16px">TEAM BIOS</h2>
    <div class="rule" style="left:16px;top:65px;width:126px"></div>
    <div class="team">
      <div class="member"><div class="photo member-photo" role="img" aria-label="Team member portrait placeholder"></div><div class="member-name">Team Member's Name</div><div class="member-role">Position</div>Short bio text about this team member goes here.</div>
      <div class="member"><div class="photo member-photo" role="img" aria-label="Team member portrait placeholder"></div><div class="member-name">Team Member's Name</div><div class="member-role">Position</div>Short bio text about this team member goes here.</div>
      <div class="member"><div class="photo member-photo" role="img" aria-label="Team member portrait placeholder"></div><div class="member-name">Team Member's Name</div><div class="member-role">Position</div>Short bio text about this team member goes here.</div>
      <div class="member"><div class="photo member-photo" role="img" aria-label="Team member portrait placeholder"></div><div class="member-name">Team Member's Name</div><div class="member-role">Position</div>Short bio text about this team member goes here.</div>
      <div class="member"><div class="photo member-photo" role="img" aria-label="Team member portrait placeholder"></div><div class="member-name">Team Member's Name</div><div class="member-role">Position</div>Short bio text about this team member goes here.</div>
      <div class="member"><div class="photo member-photo" role="img" aria-label="Team member portrait placeholder"></div><div class="member-name">Team Member's Name</div><div class="member-role">Position</div>Short bio text about this team member goes here.</div>
    </div>
  </article>
</section>

<!-- Row 4: values / services -->
<section class="sheet" style="left:67px;top:908px">
  <article class="page">
    <header class="page-head"><div class="brand"><span class="brand-mark"></span>VORNELQUAY</div><span class="folio">10</span></header>
    <div class="photo" style="left:0;top:22px;width:156px;height:113px" role="img" aria-label="Red glowing padlocks over circuitry"></div>
    <h2 class="section-title" style="left:20px;top:154px;font-size:15px">OUR VALUES</h2>
    <div class="rule" style="left:18px;top:175px;width:124px"></div>
    <div class="body-copy" style="left:18px;top:184px;width:124px"><p>Our team protects the systems, people and data that keep modern organisations running. We combine offensive testing with steady defensive practice so that every client gains a clear view of real risk, a plan to reduce it and a partner who stays close after the report is delivered. Founded by practitioners, the firm grew from a small consulting desk into a full security practice serving public and private clients across many sectors.</p></div>
  </article>
  <article class="page">
    <header class="page-head"><div class="brand"><span class="brand-mark"></span>VORNELQUAY</div><span class="folio">11</span></header>
    <h2 class="section-title" style="left:16px;top:43px;font-size:15px">OUR SERVICES</h2>
    <div class="rule" style="left:16px;top:67px;width:124px"></div>
    <div class="services">
      <div class="service"><div class="service-head">Penetration Testing<svg viewBox="0 0 10 10" fill="none" stroke="#fff" stroke-width=".9"><rect x="1.5" y="2" width="7" height="5"/><path d="M3 9h4"/></svg></div><p class="service-copy">Short description of this service goes here.</p></div>
      <div class="service"><div class="service-head">Red Team/Threat Emulation<svg viewBox="0 0 10 10" fill="none" stroke="#fff" stroke-width=".9"><circle cx="5" cy="3.5" r="2"/><path d="M1.5 9a3.5 3.5 0 0 1 7 0"/></svg></div><p class="service-copy">Short description of this service goes here.</p></div>
      <div class="service"><div class="service-head">Cloud Security Assessments<svg viewBox="0 0 10 10" fill="none" stroke="#fff" stroke-width=".9"><path d="M2.5 8h5.5a2 2 0 0 0 0-4 3 3 0 0 0-5.8.6A1.8 1.8 0 0 0 2.5 8z"/></svg></div><p class="service-copy">Short description of this service goes here.</p></div>
      <div class="service"><div class="service-head">Vulnerability Management<svg viewBox="0 0 10 10" fill="none" stroke="#fff" stroke-width=".9"><rect x="2.5" y="4.5" width="5" height="4"/><path d="M3.5 4.5V3a1.5 1.5 0 0 1 3 0v1.5"/></svg></div><p class="service-copy">Short description of this service goes here.</p></div>
      <div class="service"><div class="service-head">Managed Detection and Response<svg viewBox="0 0 10 10" fill="none" stroke="#fff" stroke-width=".9"><rect x="1.5" y="1.5" width="7" height="7"/><circle cx="5" cy="5" r="1.6"/></svg></div><p class="service-copy">Short description of this service goes here.</p></div>
      <div class="service"><div class="service-head">Incident Response<svg viewBox="0 0 10 10" fill="none" stroke="#fff" stroke-width=".9"><path d="M5 1l3.5 1.3v2.5C8.5 7 5 9 5 9S1.5 7 1.5 4.8V2.3z"/><path d="M3.7 3.8l2.6 2.6M6.3 3.8L3.7 6.4"/></svg></div><p class="service-copy">Short description of this service goes here.</p></div>
      <div class="service"><div class="service-head">Threat Hunting<svg viewBox="0 0 10 10" fill="none" stroke="#fff" stroke-width=".9"><circle cx="4.2" cy="4.2" r="2.7"/><path d="M6.2 6.2L9 9"/></svg></div><p class="service-copy">Short description of this service goes here.</p></div>
      <div class="service"><div class="service-head">Risk Assessments<svg viewBox="0 0 10 10" fill="none" stroke="#fff" stroke-width=".9"><path d="M5 1l3.5 1.3v2.5C8.5 7 5 9 5 9S1.5 7 1.5 4.8V2.3z"/><path d="M3.5 5l1.1 1.1L6.6 4"/></svg></div><p class="service-copy">Short description of this service goes here.</p></div>
      <div class="service"><div class="service-head">Simulated Phishing Campaigns<svg viewBox="0 0 10 10" fill="none" stroke="#fff" stroke-width=".9"><rect x="1" y="2.5" width="8" height="5.5"/><path d="M1 2.5l4 3 4-3"/></svg></div><p class="service-copy">Short description of this service goes here.</p></div>
    </div>
  </article>
</section>

<!-- Row 4: projects -->
<section class="sheet" style="left:395px;top:908px">
  <article class="page" style="background:#d4d4d4">
    <header class="page-head"><div class="brand"><span class="brand-mark"></span>VORNELQUAY</div><span class="folio">12</span></header>
    <h2 class="section-title" style="left:16px;top:40px;font-size:15px">PROJECTS</h2>
    <div class="rule" style="left:14px;top:62px;width:126px"></div>
    <div class="body-copy" style="left:16px;top:72px;width:124px">
      <p>Our team protects the systems, people and data that keep modern organisations running. We combine offensive testing with steady defensive practice so that every client gains a clear view of real risk, a plan to reduce it and a partner who stays close after the report is delivered. Founded by practitioners, the firm grew from a small consulting desk into a full security practice serving public and private clients across many sectors.</p>
      <p>Our team protects the systems, people and data that keep modern organisations running. We combine offensive testing with steady defensive practice so that every client gains a clear view of real risk, a plan to reduce it and a partner who stays close after the report is delivered. Founded by practitioners, the firm grew from a small consulting desk into a full security practice serving public and private clients across many sectors.</p>
    </div>
    <div class="photo" style="left:0;top:170px;width:156px;height:64px" role="img" aria-label="Red circuit board with a glowing padlock"></div>
  </article>
  <article class="page" style="background:#e9e9e9"></article>
</section>

</body>
</html>
```